Diverse, up-scale salon needs eye-catching, unique business cards.

We are looking for a unique business card design for our stylist but that can also be multi functional and used for appointment reminder and referrals. I will need a design in a format that I can modify names and titles going forward. In the past we have had a dark background with the logo on one side, and stylist and contact information on the other but we are open to all ideas. I have included our mission statement as well as branded colors below. The statement doesn't need to go on the card, it's just a reference for target market. We need space for the stylists name, title, instagram handle and then the salons phone number, website and address. I am also open to adding a spot for a qr code linked to the stylist instagram or the salon booking link.

primary brand colors:
#333333 #233415 #36502a #93874a #000000
Mission statement:
Vessolin Hair Studio, a high-end salon located in the lively Downtown Farmington, Michigan, is committed to providing exceptional services in a welcoming and relaxed environment to meet the needs of our diverse clientele.
Our salon specializes in contemporary custom haircuts, coloring, extensions, and barbering and beard grooming services. Our team of skilled stylists is passionate and inventive in their hair styling techniques. At the heart of our salon are values centered on quality, innovation, creativity, and above all, comfort. These core values are evident in every appointment across our customizable array of services.
Our goal is to establish a benchmark for exceptional hair care for every human.
Website: www.vessolinhairstudio.example
instagram: @vessolinhairstudio
address: 41782 Pelham Crest Rd, Farmington MI
phone: 248-613-4087

Industry/Entity Type

Hair Salon

Contact Information for Business Card

Stylist name, title, phone, instagram, website, address, (optional qr code)

Requirements
Should not have
• Does not need mission statement on the card.

```html
<!DOCTYPE html>
<html lang="en">
<head>
<meta charset="utf-8">
<title>Vessolin Hair Studio – Business Cards</title>
<link rel="stylesheet" href="https://fonts.googleapis.com/css2?family=Kaushan+Script&family=Nunito+Sans:wght@400;600;700&display=swap">
<style>
  :root {
    --backdrop: #1c1b1b;
    --card-dark: #222222;
    --card-light: #fbfbfb;
    --gold: #93874a;
    --white: #ffffff;
    --black: #111111;
  }
  * { box-sizing: border-box; margin: 0; padding: 0; }
  html, body { width: 1200px; height: 2811px; overflow: hidden; }
  body { background: var(--backdrop); font-family: "Nunito Sans", sans-serif; }

  .variant { position: relative; width: 1200px; height: 937px; }

  .card {
    position: absolute; width: 560px; height: 320px;
    border-radius: 18px; background: var(--card-bg);
    box-shadow: 0 14px 30px rgba(0,0,0,.55);
    color: var(--ink);
  }
  .card--front { left: 190px; top: 120px; }
  .card--back { left: 450px; top: 490px; }

  .card__frame {
    position: absolute; inset: 13px;
    border: 1.3px solid var(--ink); border-radius: 12px;
  }

  .variant--gold { --card-bg: var(--card-dark); --ink: var(--gold); }
  .variant--white { --card-bg: var(--card-dark); --ink: var(--white); }
  .variant--light { --card-bg: var(--card-light); --ink: var(--black); }

  .brand {
    position: absolute; left: 0; right: 0; top: 50%;
    transform: translateY(-50%);
    display: flex; align-items: center; justify-content: center; gap: 16px;
  }
  .brand__dot {
    width: 22px; height: 22px; border-radius: 50%;
    border: 2px solid var(--ink);
  }
  .brand__name {
    font-weight: 700; font-size: 26px; letter-spacing: 4px;
    text-transform: uppercase; line-height: 1.25;
  }

  .back__brand {
    position: absolute; left: 60px; top: 110px; width: 190px;
    font-weight: 700; font-size: 24px; letter-spacing: 3px;
    text-transform: uppercase; line-height: 1.3;
  }

  .stylist { position: absolute; left: 290px; top: 52px; }
  .stylist__name { font-family: "Kaushan Script", cursive; font-size: 34px; line-height: 1.1; }
  .stylist__title { font-size: 14px; margin-top: 2px; }
  .stylist__rule { width: 32px; height: 1.5px; background: var(--ink); margin: 14px 0 10px; }
  .contact { list-style: none; font-size: 13.5px; line-height: 1.55; }

  .address {
    position: absolute; left: 50%; bottom: 7px; transform: translateX(-20%);
    padding: 0 10px; background: var(--card-bg);
    font-size: 10.5px; font-weight: 600; letter-spacing: 1.6px;
    text-transform: uppercase; white-space: nowrap;
  }
</style>
</head>
<body>

<section class="variant variant--gold">
  <article class="card card--front">
    <div class="card__frame"></div>
    <div class="brand"><span class="brand__dot"></span><span class="brand__name">Vessolin<br>Hair Studio</span></div>
  </article>
  <article class="card card--back">
    <div class="card__frame"></div>
    <p class="back__brand">Vessolin Hair Studio</p>
    <div class="stylist">
      <h2 class="stylist__name">Marcus Dellway</h2>
      <p class="stylist__title">Owner / Hair Stylist</p>
      <div class="stylist__rule"></div>
      <ul class="contact">
        <li>248-613-4087</li>
        <li>hello@vessolinhairstudio.example</li>
        <li>www.vessolinhairstudio.example</li>
        <li>@vessolinhairstudio</li>
      </ul>
    </div>
    <p class="address">41782 Pelham Crest Rd, Farmington MI</p>
  </article>
</section>

<section class="variant variant--white">
  <article class="card card--front">
    <div class="card__frame"></div>
    <div class="brand"><span class="brand__dot"></span><span class="brand__name">Vessolin<br>Hair Studio</span></div>
  </article>
  <article class="card card--back">
    <div class="card__frame"></div>
    <p class="back__brand">Vessolin Hair Studio</p>
    <div class="stylist">
      <h2 class="stylist__name">Marcus Dellway</h2>
      <p class="stylist__title">Owner / Hair Stylist</p>
      <div class="stylist__rule"></div>
      <ul class="contact">
        <li>248-613-4087</li>
        <li>hello@vessolinhairstudio.example</li>
        <li>www.vessolinhairstudio.example</li>
        <li>@vessolinhairstudio</li>
      </ul>
    </div>
    <p class="address">41782 Pelham Crest Rd, Farmington MI</p>
  </article>
</section>

<section class="variant variant--light">
  <article class="card card--front">
    <div class="card__frame"></div>
    <div class="brand"><span class="brand__dot"></span><span class="brand__name">Vessolin<br>Hair Studio</span></div>
  </article>
  <article class="card card--back">
    <div class="card__frame"></div>
    <p class="back__brand">Vessolin Hair Studio</p>
    <div class="stylist">
      <h2 class="stylist__name">Marcus Dellway</h2>
      <p class="stylist__title">Owner / Hair Stylist</p>
      <div class="stylist__rule"></div>
      <ul class="contact">
        <li>248-613-4087</li>
        <li>hello@vessolinhairstudio.example</li>
        <li>www.vessolinhairstudio.example</li>
        <li>@vessolinhairstudio</li>
      </ul>
    </div>
    <p class="address">41782 Pelham Crest Rd, Farmington MI</p>
  </article>
</section>

</body>
</html>
```